Media Services Start-up -- Corporate Website and Logo Design. Inspiration required!

We need a logo design and corporate website design, including coding, for our start-up business.
Vennatra’s value proposition is based on bringing together media content from a vast number of geographies globally, adding human and AI curation, translation and editing, and delivering the content using tailored customer interfaces. On the one hand, the business brings together media coverage from all over the world, and on the other it brings together content, human skills and technology to deliver a supreme customer experience.
Vennatra is a B2B media monitoring and analytics business with emphasis on global customers. Vennatra's service offering is centred around sourcing media content from different markets, processing, storing and delivering the content and insights derived from it using an online platform / mobile app.
The messaging we want to create through the logo is:
- Global scope
- Speed of delivery
- Cost-efficiency
- Multi-lingual
- Tailor-made
- Trustworthy
Target Market(s)
Business to business, PR / Communications, Media, Marketing
Logo Text
Vennatra
Coding
Coded - Design and coding required
Number of Pages Required
5+ page
Font styles to use
Other font styles liked:
- See Design Brief for details
Colors
Designer to choose colors to be used in the design.

```html
<!DOCTYPE html>
<html lang="en">
<head>
<meta charset="utf-8">
<title>Vennatra — Our Solutions</title>
<link href="https://fonts.googleapis.com/css2?family=Roboto:wght@300;400;500;700&display=swap" rel="stylesheet">
<style>
  :root {
    --teal: #3aae9c;
    --ink: #5a5a5a;
    --nav: #666666;
    --white: #ffffff;
    --hero-dark: #050505;
    --hero-mid: #2c2c2c;
    --rule: #e6e6e6;
  }
  * { margin: 0; padding: 0; box-sizing: border-box; }
  html, body { width: 1200px; height: 748px; overflow: hidden; }
  body { font-family: 'Roboto', sans-serif; background: var(--white); position: relative; }

  .site-header { position: absolute; left: 0; top: 0; width: 1200px; height: 85px; background: var(--white); }
  .brand { position: absolute; left: 141px; top: 14px; font-size: 46px; font-weight: 500; color: var(--ink); letter-spacing: -0.5px; }
  .contact-bar { position: absolute; top: 10px; right: 141px; display: flex; gap: 26px; font-size: 14px; font-weight: 300; color: var(--nav); }
  .contact-item { display: flex; align-items: center; gap: 9px; }
  .contact-icon { width: 27px; height: 27px; border: 1px solid var(--teal); border-radius: 50%; display: flex; align-items: center; justify-content: center; }
  .main-nav { position: absolute; top: 49px; right: 141px; display: flex; align-items: center; font-size: 14px; font-weight: 300; color: var(--nav); }
  .main-nav a { color: inherit; text-decoration: none; margin-right: 26px; }
  .main-nav .sign-in { margin: 0 0 0 -2px; background: var(--teal); color: var(--white); font-weight: 400; font-size: 15px; width: 85px; height: 29px; display: flex; align-items: center; justify-content: center; }

  .hero { position: absolute; left: 0; top: 85px; width: 1200px; height: 627px; overflow: hidden; color: var(--white); }
  .hero-backdrop { position: absolute; inset: 0;
    background: radial-gradient(ellipse 260px 230px at 600px 230px, #3a3a3a 0%, #1d1d1d 55%, transparent 100%),
                linear-gradient(180deg, var(--hero-mid) 0%, #1a1a1a 45%, var(--hero-dark) 100%); }
  .hero-title { position: absolute; top: 51px; width: 100%; text-align: center; font-size: 34px; font-weight: 700; }
  .hero-intro { position: absolute; top: 108px; width: 100%; text-align: center; font-size: 14px; font-weight: 500; line-height: 20px; }

  .solution-tabs { position: absolute; top: 180px; left: 162px; width: 876px; height: 72px; }
  .tab { position: absolute; transform: translateX(-50%); text-align: center; font-size: 16px; font-weight: 400; white-space: nowrap; letter-spacing: 0.2px; }
  .tab svg { display: block; margin: 0 auto 8px; }
  .tab.active { font-weight: 500; }
  .tab-rule { position: absolute; left: 0; top: 70px; width: 876px; height: 2px; background: var(--rule); }
  .tab-rule .active-bar { position: absolute; left: 316px; top: -1px; width: 166px; height: 3px; background: var(--teal); }

  .solution-points { position: absolute; top: 305px; width: 100%; text-align: center; font-size: 14px; font-weight: 400; line-height: 32.5px; list-style: none; }
  .slider-arrow { position: absolute; top: 411px; width: 32px; height: 32px; border: 1px solid var(--white); display: flex; align-items: center; justify-content: center; }
  .slider-arrow.prev { left: 93px; }
  .slider-arrow.next { left: 1075px; }
  .cta { position: absolute; left: 508px; top: 507px; width: 184px; height: 36px; background: var(--teal); color: var(--white); font-size: 15.5px; display: flex; align-items: center; justify-content: center; text-decoration: none; }

  .site-footer { position: absolute; left: 0; top: 712px; width: 1200px; height: 36px; background: var(--teal); color: var(--white); }
  .copyright { position: absolute; left: 141px; top: 10px; font-size: 13px; font-weight: 300; }
  .social { position: absolute; right: 141px; top: 11px; display: flex; gap: 10px; }
  .social span { width: 14px; height: 14px; border-radius: 50%; background: var(--white); display: block; }
</style>
</head>
<body>
  <header class="site-header">
    <div class="brand">Vennatra</div>
    <div class="contact-bar">
      <div class="contact-item">
        <span class="contact-icon">
          <svg width="13" height="13" viewBox="0 0 24 24"><path d="M6.6 10.8a15 15 0 0 0 6.6 6.6l2.2-2.2c.3-.3.7-.4 1-.2 1.1.4 2.3.6 3.6.6.6 0 1 .4 1 1V20c0 .6-.4 1-1 1A17 17 0 0 1 3 4c0-.6.4-1 1-1h3.5c.6 0 1 .4 1 1 0 1.3.2 2.5.6 3.6.1.3 0 .7-.2 1z" fill="#555"/></svg>
        </span>+1 555 014 2288
      </div>
      <div class="contact-item">
        <span class="contact-icon">
          <svg width="13" height="10" viewBox="0 0 26 18"><rect x="1" y="1" width="24" height="16" fill="none" stroke="#555" stroke-width="2"/><path d="M1 1l12 9 12-9" fill="none" stroke="#555" stroke-width="2"/></svg>
        </span>info@vennatra.com
      </div>
    </div>
    <nav class="main-nav">
      <a href="#">Home</a><a href="#">Solutions</a><a href="#">How We Do It</a><a href="#">Our People</a><a href="#">Our Technology</a>
      <a href="#" class="sign-in">SIGN IN</a>
    </nav>
  </header>

  <section class="hero">
    <div class="hero-backdrop" role="img" aria-label="Night city skyline with a glowing globe, network lines and floating industry icons"></div>
    <h1 class="hero-title">Our Solutions</h1>
    <p class="hero-intro">Lorem ipsum dolor sit amet, consectetuer adipiscing elit, sed diam nonummy nibh<br>euismod tincidunt ut laoreet dolore magna aliquam erat volutpat.</p>

    <div class="solution-tabs">
      <div class="tab" style="left:65px">
        <svg width="30" height="30" viewBox="0 0 30 30"><circle cx="15" cy="9" r="6" fill="#fff"/><rect x="3" y="17" width="13" height="9" fill="none" stroke="#fff" stroke-width="2"/><rect x="19" y="15" width="8" height="12" fill="none" stroke="#fff" stroke-width="2"/></svg>
        Content Sourcing</div>
      <div class="tab" style="left:223px">
        <svg width="30" height="30" viewBox="0 0 30 30"><circle cx="15" cy="10" r="8" fill="#fff"/><rect x="9" y="17" width="12" height="4" fill="#fff"/><circle cx="7" cy="26" r="3" fill="#fff"/><circle cx="15" cy="26" r="3" fill="#fff"/><circle cx="23" cy="26" r="3" fill="#fff"/></svg>
        Content Collection</div>
      <div class="tab active" style="left:401px">
        <svg width="32" height="32" viewBox="0 0 32 32"><path d="M3 3l26 26M29 3L3 29" stroke="#3aae9c" stroke-width="2"/><circle cx="16" cy="10" r="4" fill="#3aae9c"/><rect x="11" y="15" width="10" height="12" rx="4" fill="#3aae9c"/></svg>
        Content Augmentation</div>
      <div class="tab" style="left:570px">
        <svg width="30" height="30" viewBox="0 0 30 30"><circle cx="15" cy="15" r="7" fill="none" stroke="#fff" stroke-width="2"/><g fill="#fff"><circle cx="15" cy="3" r="2"/><circle cx="15" cy="27" r="2"/><circle cx="3" cy="15" r="2"/><circle cx="27" cy="15" r="2"/><circle cx="6.5" cy="6.5" r="2"/><circle cx="23.5" cy="23.5" r="2"/><circle cx="23.5" cy="6.5" r="2"/><circle cx="6.5" cy="23.5" r="2"/></g></svg>
        Content Delivery</div>
      <div class="tab" style="left:765px">
        <svg width="34" height="30" viewBox="0 0 34 30"><ellipse cx="25" cy="8" rx="8" ry="6" fill="#fff"/><circle cx="13" cy="15" r="4" fill="#fff"/><path d="M4 28c0-6 4-9 9-9s9 3 9 9z" fill="#fff"/></svg>
        Media Insights &amp; Consultancy</div>
      <div class="tab-rule"><span class="active-bar"></span></div>
    </div>

    <ul class="solution-points">
      <li>We manage and normalise all of the source-level reference data - country, language, reach etc.</li>
      <li>We add editorial validation to ensure only the content required reaches your delivery, removing inevitable noise from source providers</li>
      <li>Tagging - AI and human based tagging to detect locations, people, topics, products, brands, services, etc.</li>
      <li>Human and automated grouping of stories across geographies - clustering, "also-in" groupings etc.</li>
      <li>Translation summarisation - AI Translation or human-created depending on budget, speed of delivery and need.</li>
      <li>Digest authoring - refining the essence of today’s coverage into a concise board-ready output for your organisation</li>
    </ul>

    <a href="#" class="slider-arrow prev" aria-label="Previous"><svg width="12" height="18" viewBox="0 0 12 18"><path d="M10 1L2 9l8 8" fill="none" stroke="#fff" stroke-width="1.5"/></svg></a>
    <a href="#" class="slider-arrow next" aria-label="Next"><svg width="12" height="18" viewBox="0 0 12 18"><path d="M2 1l8 8-8 8" fill="none" stroke="#fff" stroke-width="1.5"/></svg></a>
    <a href="#" class="cta">CONTACT US TODAY</a>
  </section>

  <footer class="site-footer">
    <p class="copyright">Copyright © 2019 Vennatra. All Rights Reserved.</p>
    <div class="social" aria-label="Social links"><span></span><span></span><span></span></div>
  </footer>
</body>
</html>
```